NEW Modern Sleek Business Card for VR Language Startup

Our startup is using VR to lead the next wave of world language education. We need a two-sided business card that introduces the larger organization (Brightloom Language Inc) and our contact info on one side and shows the product, Glimwoorld, on the other side.

Side 1 (contact info)= Brightloom Logo and Contact info (name, title, phone, email)

Side 2 (product)= Glimworld logo, text, and website
Text= Culturally Immersive Language Learning Games
Website= www.glimworld-play.com

Target Market(s)

Education, Technology

Contact Information for Business Card

Contact info will be updated upon approval of the design. For now, put this as a placeholder.

Perry Dunmore
Founder & CEO
pdunmore@quillpost-mail.net
(555)-014-2286

Font styles to use
Other font styles liked:
• Gibson and Century Gothic are the brand fonts

Requirements
Nice to have
• I would love to see cohesion between the design and colors of the two logos. I have attached a few business card designs that I like, so you can get a feel for my preferred style.

```html
<!DOCTYPE html>
<html lang="en">
<head>
<meta charset="utf-8">
<title>Brightloom Language – Business Card</title>
<link rel="stylesheet" href="https://fonts.googleapis.com/css2?family=Questrial&family=Roboto:wght@400;500&display=swap">
<style>
  :root {
    --backdrop: #9b9b9b;
    --card-dark: #000000;
    --card-light: #ffffff;
    --edge: #f4912b;
    --ink: #1d1d1f;
    --ink-soft: #4a4a4a;
    --rule: #9a9a9a;
    --brand-blue: #2f9ff0;
    --brand-orange: #f7941d;
    --product-blue: #1f3ff0;
    --product-cyan: #19b6f0;
    --white: #ffffff;
  }
  * { box-sizing: border-box; margin: 0; padding: 0; }
  html, body { width: 1200px; height: 960px; overflow: hidden; }
  body {
    background: var(--backdrop);
    font-family: "Questrial", "Century Gothic", sans-serif;
    position: relative;
  }
  .card {
    position: absolute;
    width: 700px;
    height: 400px;
    border-radius: 2px;
    box-shadow: 0 4px 0 var(--edge), 0 14px 30px rgba(0,0,0,.28);
    overflow: hidden;
  }

  /* Product side */
  .card--product { left: 170px; top: 50px; background: var(--card-dark); color: var(--white); }
  .product-mark {
    position: absolute; left: 0; right: 0; top: 62px;
    display: flex; flex-direction: column; align-items: center; gap: 10px;
  }
  .product-mark__dot {
    width: 96px; height: 96px; border-radius: 50%;
    background: linear-gradient(135deg, var(--product-cyan), var(--product-blue));
  }
  .product-mark__name { font-size: 48px; line-height: 1; color: var(--white); letter-spacing: .5px; }
  .product-tagline {
    position: absolute; left: 0; right: 0; top: 238px;
    text-align: center; font-size: 17px; letter-spacing: .3px;
  }
  .product-web {
    position: absolute; left: 0; right: 0; top: 272px;
    display: flex; align-items: center; justify-content: center; gap: 10px;
    color: var(--product-blue); font-size: 16px;
  }
  .product-web svg { display: block; }

  /* Contact side */
  .card--contact { left: 330px; top: 500px; background: var(--card-light); color: var(--ink); }
  .company-mark {
    position: absolute; right: 46px; top: 40px;
    display: flex; align-items: flex-end; gap: 16px;
  }
  .company-mark__dot {
    width: 72px; height: 72px; border-radius: 50%;
    margin-bottom: -22px;
    background: linear-gradient(135deg, var(--brand-orange), #e8356d 50%, #27c6f0);
  }
  .company-mark__name {
    display: flex; flex-direction: column; align-items: flex-start;
    color: var(--ink); font-weight: 400; line-height: 1;
  }
  .company-mark__line1 { font-size: 38px; letter-spacing: 4px; text-transform: uppercase; }
  .company-mark__line2 { font-size: 17px; letter-spacing: 12.5px; text-transform: uppercase; margin-top: 10px; padding-left: 4px; }
  .holder { position: absolute; left: 50px; top: 226px; }
  .holder__name { font-family: "Roboto", sans-serif; font-weight: 500; font-size: 30px; color: var(--brand-blue); line-height: 1.1; }
  .holder__title { font-family: "Roboto", sans-serif; font-weight: 400; font-size: 20px; color: var(--brand-orange); }
  .divider { position: absolute; left: 50px; right: 50px; top: 300px; height: 1px; background: var(--rule); }
  .company-web {
    position: absolute; right: 50px; top: 312px;
    font-family: "Roboto", sans-serif; font-size: 16px; color: var(--ink-soft);
  }
  .contact-list {
    position: absolute; left: 50px; top: 316px; list-style: none;
    font-family: "Roboto", sans-serif; font-size: 17px; color: var(--ink-soft);
  }
  .contact-list li { display: flex; align-items: center; gap: 10px; margin-bottom: 8px; }
  .contact-list svg { display: block; fill: var(--brand-blue); }
</style>
</head>
<body>

<section class="card card--product" aria-label="Product side">
  <div class="product-mark">
    <span class="product-mark__dot"></span>
    <span class="product-mark__name">Glimworld</span>
  </div>
  <p class="product-tagline">Culturally Immersive Language Learning Games</p>
  <div class="product-web">
    <svg width="130" height="10" viewBox="0 0 130 10" aria-hidden="true">
      <line x1="0" y1="5" x2="122" y2="5" stroke="#1f3ff0" stroke-width="1"/>
      <circle cx="125" cy="5" r="3.5" fill="none" stroke="#1f3ff0" stroke-width="1.2"/>
    </svg>
    <span>www.glimworld-play.com</span>
    <svg width="130" height="10" viewBox="0 0 130 10" aria-hidden="true">
      <circle cx="5" cy="5" r="3.5" fill="none" stroke="#1f3ff0" stroke-width="1.2"/>
      <line x1="8" y1="5" x2="130" y2="5" stroke="#1f3ff0" stroke-width="1"/>
    </svg>
  </div>
</section>

<section class="card card--contact" aria-label="Contact side">
  <div class="company-mark">
    <span class="company-mark__dot"></span>
    <span class="company-mark__name">
      <span class="company-mark__line1">Brightloom</span>
      <span class="company-mark__line2">Language</span>
    </span>
  </div>

  <div class="holder">
    <p class="holder__name">Perry Dunmore</p>
    <p class="holder__title">Founder &amp; CEO</p>
  </div>

  <div class="divider"></div>
  <p class="company-web">www.brightloomlanguage.com</p>

  <ul class="contact-list">
    <li>
      <svg width="16" height="16" viewBox="0 0 24 24" aria-hidden="true"><path d="M6.6 10.8a15.1 15.1 0 0 0 6.6 6.6l2.2-2.2a1 1 0 0 1 1-.25 11.4 11.4 0 0 0 3.6.57 1 1 0 0 1 1 1V20a1 1 0 0 1-1 1A17 17 0 0 1 3 4a1 1 0 0 1 1-1h3.5a1 1 0 0 1 1 1c0 1.25.2 2.45.57 3.57a1 1 0 0 1-.25 1z"/></svg>
      <span>(555)-014-2286</span>
    </li>
    <li>
      <svg width="16" height="16" viewBox="0 0 24 24" aria-hidden="true"><path d="M2 5h20v14H2z" fill="#2f9ff0"/><path d="M3 6l9 7 9-7" fill="none" stroke="#fff" stroke-width="1.6"/></svg>
      <span>pdunmore@quillpost-mail.net</span>
    </li>
  </ul>
</section>

</body>
</html>
```